New Business Card for Web Design/Internet Marketing Company

Looking for a great looking new business card. We are a 10 year old web design, internet marketing and website management company that works mostly with small businesses.

Our new card needs to better match the colors and style of our website, be bold, extremely usable and slightly edgy.

Target Market(s)

Small/Medium businesses that have websites

Industry/Entity Type

Internet

Requirements
Must have
• Front and back design, full color, rounded corners please

Must use the colors/style of our website (JPG provided)

INFO FOR CARDS (as readable as possible please)
Mark Lenner
President/CEO
mark@trelvanmedia.example
Phone: 520-381-7459
Toll Free: 866-381-7459
Address: 4315 W. Calloway Ave. Ste. 140, Tucson, AZ 85792

THINGS I WANT TO PROMOTE (if there is room):
1. Our Website - www.trelvanmedia.example

2. Social Media
Twitter: @trelvanmedia
Facebook: www.facebook.com/trelvanmedia

3. Our Services
Web Design
Internet Marketing
Website Management

```html
<!DOCTYPE html>
<html lang="en">
<head>
<meta charset="utf-8">
<title>Trelvan Media – Business Card</title>
<link rel="stylesheet" href="https://fonts.googleapis.com/css2?family=Ubuntu:wght@400;500;700&display=swap">
<style>
  :root {
    --navy: #1f3a6b;
    --sky: #1b8fcb;
    --orange: #f08a3c;
    --ink: #4a4a4a;
    --rule: #9a9a9a;
    --social: #6fb3e0;
    --paper: #ffffff;
    --backdrop: #e9e6e1;
  }
  * { box-sizing: border-box; margin: 0; padding: 0; }
  html, body {
    width: 1200px; height: 402px; overflow: hidden;
    background: var(--backdrop);
    font-family: "Ubuntu", sans-serif;
  }
  .sheet { position: relative; width: 1200px; height: 402px; }
  .card {
    position: absolute; top: 60px;
    width: 512px; height: 292px;
    border-radius: 6px; overflow: hidden;
  }
  .card--front { left: 64px; background: var(--paper); }
  .card--back { left: 629px; background: var(--navy); color: var(--paper); }

  /* front */
  .brand {
    position: absolute; top: 58px; left: 0; width: 100%;
    display: flex; align-items: center; justify-content: center; gap: 12px;
  }
  .brand__dot { width: 34px; height: 34px; border-radius: 50%; background: var(--sky); }
  .brand__name { font-size: 40px; font-weight: 700; color: var(--orange); letter-spacing: -0.5px; }
  .person { position: absolute; top: 134px; width: 100%; text-align: center; }
  .person__name { font-size: 17px; font-weight: 700; color: var(--sky); }
  .person__title { font-size: 12px; font-weight: 400; color: var(--sky); }
  .person__email {
    margin-top: 2px; font-size: 12.5px; color: var(--ink);
    display: flex; align-items: center; justify-content: center; gap: 5px;
  }
  .contact {
    position: absolute; top: 186px; left: 0; width: 100%;
    display: flex; justify-content: center; gap: 10px;
    font-size: 12.5px; color: var(--ink); line-height: 17px;
  }
  .contact__phones { text-align: left; padding-right: 10px; border-right: 1px solid var(--rule); }
  .contact__phones div { display: flex; align-items: center; gap: 4px; }
  .icon { width: 10px; height: 10px; flex: none; }
  .front-band { position: absolute; left: 0; bottom: 0; width: 512px; height: 70px; }
  .front-band__url {
    position: absolute; bottom: 11px; width: 100%; text-align: center;
    font-size: 15px; font-weight: 500; color: var(--paper);
  }

  /* back */
  .back-brand {
    position: absolute; top: 72px; width: 100%;
    display: flex; align-items: center; justify-content: center; gap: 12px;
  }
  .back-brand__dot { width: 30px; height: 30px; border-radius: 50%; background: var(--paper); }
  .back-brand__name { font-size: 38px; font-weight: 700; color: var(--paper); }
  .services {
    position: absolute; top: 186px; width: 100%; text-align: center;
    font-size: 18px; line-height: 26px;
  }
  .social {
    position: absolute; top: 264px; width: 100%;
    display: flex; justify-content: center; gap: 36px;
    font-size: 12.5px;
  }
  .social__item { display: flex; align-items: center; gap: 5px; }
  .social__mark { width: 12px; height: 12px; border-radius: 2px; background: var(--social); }
</style>
</head>
<body>
<main class="sheet">

  <section class="card card--front" aria-label="Card front">
    <div class="brand">
      <span class="brand__dot"></span>
      <span class="brand__name">Trelvan Media</span>
    </div>

    <div class="person">
      <p><span class="person__name">Mark Lenner,</span> <span class="person__title">President/CEO</span></p>
      <p class="person__email">
        <svg class="icon" viewBox="0 0 10 8"><rect width="10" height="8" rx="1" fill="#1b8fcb"/><path d="M0.5 1 L5 4.5 L9.5 1" stroke="#fff" stroke-width="1" fill="none"/></svg>
        mark@trelvanmedia.example
      </p>
    </div>

    <div class="contact">
      <div class="contact__phones">
        <div><svg class="icon" viewBox="0 0 10 10"><circle cx="5" cy="5" r="5" fill="#1b8fcb"/><path d="M3 2.5 L4.2 2.5 L4.6 4 L4 4.5 Q4.8 6 6 6.4 L6.5 5.8 L7.8 6.2 L7.8 7.4 Q4 7.6 3 2.5Z" fill="#fff"/></svg>520-381-7459</div>
        <div><svg class="icon" viewBox="0 0 10 10"><circle cx="5" cy="5" r="5" fill="#1b8fcb"/><path d="M3 2.5 L4.2 2.5 L4.6 4 L4 4.5 Q4.8 6 6 6.4 L6.5 5.8 L7.8 6.2 L7.8 7.4 Q4 7.6 3 2.5Z" fill="#fff"/></svg>866-381-7459</div>
      </div>
      <div class="contact__address">
        <div>4315 W. Calloway Ave.</div>
        <div>Ste. 140, Tucson, AZ 85792</div>
      </div>
    </div>

    <svg class="front-band" viewBox="0 0 512 70" preserveAspectRatio="none" aria-hidden="true">
      <path d="M0 32 Q240 4 472 22" stroke="#1b8fcb" stroke-width="4" fill="none"/>
      <path d="M0 42 Q256 18 512 30 L512 70 L0 70Z" fill="#1f3a6b"/>
    </svg>
    <p class="front-band__url">www.trelvanmedia.example</p>
  </section>

  <section class="card card--back" aria-label="Card back">
    <div class="back-brand">
      <span class="back-brand__dot"></span>
      <span class="back-brand__name">Trelvan Media</span>
    </div>
    <div class="services">
      <p>Web Design &nbsp;•&nbsp; Internet Marketing</p>
      <p>Website Management</p>
    </div>
    <div class="social">
      <span class="social__item"><span class="social__mark"></span>@trelvanmedia</span>
      <span class="social__item"><span class="social__mark"></span>trelvanmedia</span>
    </div>
  </section>

</main>
</body>
</html>
```